Create book cover for a Sudoku puzzle book

It is a sudoku puzzle book for experienced sudoku puzzle solvers. It has over 250 sudoku puzzles ranging from medium level to hard.

Create a book cover closely refer to the reference image. The book cover must look as similar to the reference image as possible, including all the design style, color, illustrations and fonts. Use the sudoku puzzle in the attachment to replace the one on the reference image. All the design elements including fonts must be commercially licensed.

In the final delivery, the cover design must be available in both png/ai and pdf file format. All source files and commercial licenses for the used design elements must also be delivered as well.

Book Title: Quill Harbor Puzzlers
Subtitle: 250+ Medium to Hard Puzzles

Book size: 8.5x11 inches
Page count: 171
Paperback Print Book
Platform: Brindlewood BPP

Text on the front cover (all in uppercase):
- Quill Harbor Puzzlers
- 250+ Medium to Hard Puzzles
- 2025
- 250+ Puzzles
- large print

Text on spine:
Book title (only title, no subtitle) on the upper part of the spine and author name on the lower part. All in uppercase.

Text on the back cover (on the top):
Thank you for purchasing "Quill Harbor Puzzlers." We hope you are enjoying the puzzles and finding them both challenging and fun. If you have a moment, please consider leaving a review on Brindlewood. Your feedback helps other puzzle enthusiasts discover this book and allows us to continue creating quality content. We appreciate your support and look forward to hearing your thoughts!

Logo on back cover:
-pen name logo, the logo size should be small and subtle. (on bottom middle)

```html
<!DOCTYPE html>
<html lang="en">
<head>
<meta charset="utf-8">
<title>Quill Harbor Puzzlers – Book Cover</title>
<link rel="stylesheet" href="https://fonts.googleapis.com/css2?family=Montserrat:ital,wght@0,500;0,700;0,800;0,900;1,500&display=swap">
<style>
  :root {
    --ink: #111316;
    --red: #e3262c;
    --white: #ffffff;
    --paper: #ffffff;
    --band: #0c0d0f;
    --badge-light: #ffd21f;
    --badge-dark: #f07a10;
    --logo-ring: #2a3442;
    --grid-line: #9a9a9a;
  }
  * { box-sizing: border-box; margin: 0; padding: 0; }
  html, body { width: 1200px; height: 765px; overflow: hidden; background: var(--paper); }
  body { font-family: "Montserrat", Arial, sans-serif; color: var(--ink); }

  .cover { position: relative; width: 1200px; height: 765px; background: var(--paper); }

  /* Back cover */
  .back-copy {
    position: absolute; left: 58px; top: 60px; width: 480px;
    font-size: 20px; font-weight: 500; line-height: 27.5px; text-align: justify;
  }
  .back-copy em { font-style: italic; }
  .imprint {
    position: absolute; left: 214px; top: 635px;
    display: flex; align-items: center; gap: 10px;
  }
  .imprint-dot { width: 26px; height: 26px; border-radius: 50%; background: var(--logo-ring); }
  .imprint-name { font-size: 15px; font-weight: 700; color: var(--logo-ring); letter-spacing: .5px; }

  /* Spine */
  .spine-title, .spine-author {
    position: absolute; left: 578px; writing-mode: vertical-rl;
    font-weight: 800; font-size: 20px; letter-spacing: .3px; white-space: nowrap;
  }
  .spine-title { top: 108px; }
  .spine-author { top: 496px; font-weight: 700; letter-spacing: 1px; }

  /* Front cover */
  .front { position: absolute; left: 612px; top: 0; width: 588px; height: 765px; overflow: hidden; }
  .kicker {
    position: absolute; top: 20px; width: 100%; text-align: center;
    font-weight: 900; font-size: 30px; letter-spacing: .5px;
  }
  .kicker .accent { color: var(--red); font-size: 38px; }
  .title-main {
    position: absolute; top: 62px; width: 100%; text-align: center;
    font-weight: 900; font-size: 68px; line-height: 78px; letter-spacing: -1px;
  }
  .title-sub {
    position: absolute; top: 146px; width: 100%; text-align: center;
    font-weight: 900; font-size: 30px; letter-spacing: .5px;
  }
  .year {
    position: absolute; top: 188px; left: 252px; width: 96px; height: 34px;
    background: var(--red); color: var(--white); border-radius: 9px;
    font-weight: 900; font-size: 26px; line-height: 34px; text-align: center;
  }
  .splash {
    position: absolute; left: 0; top: 228px; width: 588px; height: 478px;
    background:
      radial-gradient(ellipse 55% 50% at 50% 55%, #1a1a1c 0%, #c81e24 28%, #2a2a2e 50%, rgba(220,40,46,.75) 66%, rgba(255,255,255,0) 88%),
      linear-gradient(180deg, #ffffff 0%, #f4f4f4 100%);
  }
  .band {
    position: absolute; left: 0; top: 705px; width: 588px; height: 60px;
    background: var(--band); color: var(--white);
    font-weight: 900; font-size: 30px; line-height: 60px; text-align: center; letter-spacing: .5px;
  }

  .puzzle {
    position: absolute; left: 186px; top: 315px; width: 201px; height: 201px;
    display: grid; grid-template-columns: repeat(9, 1fr); grid-template-rows: repeat(9, 1fr);
    background: var(--white); border: 2.5px solid var(--ink);
  }
  .cell {
    border-right: 1px solid var(--grid-line); border-bottom: 1px solid var(--grid-line);
    font-weight: 700; font-size: 15px; display: flex; align-items: center; justify-content: center;
  }
  .cell:nth-child(9n) { border-right: none; }
  .cell:nth-child(9n+3), .cell:nth-child(9n+6) { border-right: 2px solid var(--ink); }
  .cell:nth-child(n+19):nth-child(-n+27), .cell:nth-child(n+46):nth-child(-n+54) { border-bottom: 2px solid var(--ink); }
  .cell:nth-child(n+73) { border-bottom: none; }

  .print-badge { position: absolute; left: 420px; top: 533px; width: 122px; height: 122px; }
  .print-badge-text {
    position: absolute; left: 420px; top: 565px; width: 122px; text-align: center;
    font-weight: 900; font-size: 22px; line-height: 26px; transform: rotate(10deg);
  }
  .print-badge-text span { font-weight: 700; font-size: 20px; }
</style>
</head>
<body>
<div class="cover">
  <p class="back-copy">Thank you for purchasing <em>"Quill Harbor Puzzlers"</em>. We hope you are enjoying the puzzles and finding them both challenging and fun. If you have a moment, please consider leaving a review on Brindlewood. Your feedback helps other puzzle enthusiasts discover this book and allows us to continue creating quality content.We appreciate your support and look forward to hearing your thoughts!</p>
  <div class="imprint"><span class="imprint-dot"></span><span class="imprint-name">ELLIS VANTOR</span></div>

  <div class="spine-title">QUILL HARBOR PUZZLERS</div>
  <div class="spine-author">ELLIS VANTOR</div>

  <section class="front">
    <div class="splash" role="img" aria-label="Explosive abstract paint splash in red, black and white radiating from the centre"></div>
    <div class="kicker"><span class="accent">250+</span> PUZZLES</div>
    <h1 class="title-main">QUILL HARBOR</h1>
    <div class="title-sub">PUZZLERS</div>
    <div class="year">2025</div>

    <div class="puzzle">
      <div class="cell">5</div><div class="cell"></div><div class="cell"></div><div class="cell"></div><div class="cell">7</div><div class="cell"></div><div class="cell"></div><div class="cell"></div><div class="cell">2</div>
      <div class="cell"></div><div class="cell">7</div><div class="cell"></div><div class="cell">1</div><div class="cell"></div><div class="cell"></div><div class="cell">3</div><div class="cell"></div><div class="cell"></div>
      <div class="cell"></div><div class="cell"></div><div class="cell">8</div><div class="cell"></div><div class="cell"></div><div class="cell">2</div><div class="cell"></div><div class="cell">6</div><div class="cell"></div>
      <div class="cell">8</div><div class="cell"></div><div class="cell"></div><div class="cell"></div><div class="cell">6</div><div class="cell"></div><div class="cell"></div><div class="cell"></div><div class="cell">3</div>
      <div class="cell"></div><div class="cell">2</div><div class="cell"></div><div class="cell">8</div><div class="cell"></div><div class="cell">3</div><div class="cell"></div><div class="cell">9</div><div class="cell"></div>
      <div class="cell">7</div><div class="cell"></div><div class="cell"></div><div class="cell"></div><div class="cell">2</div><div class="cell"></div><div class="cell"></div><div class="cell"></div><div class="cell">6</div>
      <div class="cell"></div><div class="cell">6</div><div class="cell"></div><div class="cell">5</div><div class="cell"></div><div class="cell"></div><div class="cell">2</div><div class="cell"></div><div class="cell"></div>
      <div class="cell"></div><div class="cell"></div><div class="cell">7</div><div class="cell"></div><div class="cell"></div><div class="cell">9</div><div class="cell"></div><div class="cell">3</div><div class="cell"></div>
      <div class="cell">3</div><div class="cell"></div><div class="cell"></div><div class="cell"></div><div class="cell">8</div><div class="cell"></div><div class="cell"></div><div class="cell"></div><div class="cell">9</div>
    </div>

    <svg class="print-badge" viewBox="0 0 120 120" aria-hidden="true">
      <defs>
        <radialGradient id="badgeFill" cx="50%" cy="40%" r="60%">
          <stop offset="0%" stop-color="#ffd21f"/>
          <stop offset="100%" stop-color="#f07a10"/>
        </radialGradient>
      </defs>
      <polygon fill="url(#badgeFill)" stroke="#ffffff" stroke-width="2"
        points="60,2 67,13 78,5 81,18 94,15 93,28 106,29 101,41 113,46 104,56 113,65 102,71 108,83 95,85 97,98 84,97 81,110 70,104 63,116 55,106 44,114 41,101 28,104 28,91 15,89 20,77 8,71 17,62 8,53 19,47 13,35 26,32 24,19 37,21 40,8 51,14"/>
    </svg>
    <div class="print-badge-text">LARGE<br><span>PRINT</span></div>

    <div class="band">250+ MEDIUM TO HARD PUZZLES</div>
  </section>
</div>
</body>
</html>
```